E learning Platform for privacy

Current website is as below and its more of a shell.
I need someone to take the text and content and design it properly.
https://study.vornaquill.com/

After that, design has to be implemented with elementor and wordpress
https://elementor.com/

```html
<!DOCTYPE html>
<html lang="en">
<head>
<meta charset="utf-8">
<title>Vornaquill Learning Centre – Episode</title>
<link href="https://fonts.googleapis.com/css2?family=Poppins:ital,wght@0,400;0,500;0,600;0,700;1,400&display=swap" rel="stylesheet">
<style>
:root{
  --ink:#1f1f2e;
  --muted:#7b7b8a;
  --line:#e6e6ea;
  --accent:#f7941d;
  --episode:#ec5a27;
  --episode-dark:#d9481a;
  --pill:#f0f0f3;
  --footer:#4a4a4b;
  --footer-arc:#f29222;
  --video-a:#2a1a8f;
  --video-b:#4527b8;
  --play:#f47b6e;
}
*{margin:0;padding:0;box-sizing:border-box}
html,body{width:734px;height:1200px;overflow:hidden;background:#fff}
body{position:relative;font-family:'Poppins',sans-serif;color:var(--ink)}
.abs{position:absolute}

/* header */
.brand{left:59px;top:14px;font-weight:700;font-size:17px;color:var(--episode);letter-spacing:.5px;line-height:1}
.brand small{display:block;font-size:4.5px;color:var(--ink);font-weight:500;letter-spacing:3px;margin-top:6px}
.nav{top:22px;font-size:9.5px;font-weight:600;line-height:12px}
.nav-title{left:233px}
.nav-rate{left:397px;display:flex;align-items:center;gap:4px}
.progress{left:505px;top:17px;display:flex;align-items:center;gap:4px;font-size:9px;color:var(--muted)}
.progress i{width:22px;height:22px;border-radius:50%;border:2px solid #eee;border-top-color:var(--accent);border-right-color:var(--accent)}
.share{left:607px;top:16px;width:58px;height:26px;border-radius:13px;background:var(--accent);color:#fff;font-size:7.5px;font-weight:600;display:flex;align-items:center;justify-content:center;gap:3px}
.kebab{left:675px;top:22px;display:flex;flex-direction:column;gap:2px}
.kebab b{width:3.5px;height:3.5px;border-radius:50%;background:var(--ink)}
.rule{left:59px;top:59px;width:617px;height:1px;background:var(--line)}

/* video */
.video{left:54px;top:102px;width:426px;height:331px;border-radius:17px;background:linear-gradient(125deg,#e3e1f7 0%,#c9c3ef 22%,var(--video-b) 23%,var(--video-a) 100%);overflow:hidden}
.video .screen{position:absolute;left:15px;top:38px;width:395px;height:254px;background:radial-gradient(circle at 63% 50%,#3b2aa8 0%,#2a1d8c 45%,#24177a 100%)}
.video .play{position:absolute;left:260px;top:206px;width:120px;height:120px;margin:-60px;border-radius:50%;background:#fff;border:6px solid var(--play);box-shadow:0 0 0 4px rgba(255,255,255,.35)}
.video .play svg{position:absolute;left:38px;top:34px}
.arrow{width:32px;height:32px;border-radius:50%;background:#fff;box-shadow:0 3px 10px rgba(0,0,0,.12);display:flex;align-items:center;justify-content:center;top:242px}

/* episode bar */
.episode{left:98px;top:455px;width:321px;height:76px;border-radius:6px;background:var(--episode);color:#fff}
.episode .thumb{position:absolute;left:11px;top:6px;width:34px;height:34px;border-radius:50%;background:linear-gradient(135deg,#7fd3f0,#3b7bd8);border:2px solid #fff}
.episode h3{position:absolute;left:50px;top:10px;font-size:8.7px;font-weight:600}
.episode .meta{position:absolute;left:50px;top:25px;font-size:6.3px;display:flex;gap:6px;align-items:center}
.episode .tags{position:absolute;left:50px;top:44px;font-size:8.7px;font-weight:600}
.tag{position:absolute;left:77px;top:41px;width:61px;height:19px;border-radius:10px;background:#fff;color:var(--ink);font-size:6px;font-weight:500;display:flex;align-items:center;justify-content:center}
.episode .divider{position:absolute;left:164px;top:14px;width:1px;height:46px;background:rgba(255,255,255,.35)}
.btn{position:absolute;left:188px;width:94px;height:20px;border-radius:10px;font-size:6px;font-weight:600;display:flex;align-items:center;justify-content:center}
.btn-sub{top:16px;background:#fff;color:var(--ink)}
.btn-watch{top:41px;background:var(--episode-dark);color:#fff}
.ico{position:absolute;left:293px;width:18px;height:18px;border-radius:50%;background:var(--episode-dark);display:flex;align-items:center;justify-content:center}
.chev{left:428px;top:487px}

/* content blocks */
.block-head{left:100px;width:321px;height:26px;border-radius:4px;background:#f2f2f4;font-size:8.7px;font-weight:500;padding:7px 11px}
.about{left:111px;top:580px;width:305px;font-size:8.2px;line-height:12px;color:#555}
.published{left:111px;top:626px;font-size:8.2px;font-style:italic;color:#aaa}
.contribute{left:100px;top:698px;width:321px;height:59px;border:1px dashed #d6d6dc;border-radius:4px;display:flex;align-items:center;gap:11px;padding-left:14px;font-size:10.5px;font-weight:500}
.avatar{width:33px;height:33px;border-radius:50%;background:linear-gradient(160deg,#d8cfc4,#f0b63a)}
.comment{left:100px;top:780px}
.comment .av{position:absolute;left:0;top:0;width:31px;height:31px;border-radius:50%;background:linear-gradient(135deg,#2d5fb8,#1a2d6b)}
.comment .name{position:absolute;left:38px;top:1px;font-size:10px;font-weight:500;color:#2c2c7a;white-space:nowrap}
.comment .name span{font-size:7.5px;color:#666;font-weight:400;margin-left:4px}
.comment .txt{position:absolute;left:38px;top:18px;font-size:7.5px;letter-spacing:1px;color:#444}
.comment .lvl{position:absolute;left:5px;top:35px;font-size:7px;color:#999;white-space:nowrap}
.comment .likes{position:absolute;left:38px;top:48px;font-size:7.5px;color:#555;display:flex;gap:3px;align-items:center}

/* sidebar */
.sidebar{left:520px;top:102px;width:159px;height:668px;border-radius:12px;background:#fff;box-shadow:0 4px 24px rgba(0,0,0,.08)}
.series-thumb{position:absolute;left:15px;top:9px;width:33px;height:33px;border-radius:50%;background:linear-gradient(135deg,#7fd3f0,#3b7bd8)}
.series-title{position:absolute;left:14px;top:46px;font-size:8.4px;font-weight:500}
.series-meta{position:absolute;left:13px;top:58px;font-size:6.3px;color:#555;display:flex;gap:6px;white-space:nowrap}
.sb-rule{position:absolute;left:10px;width:140px;height:1px;background:var(--line)}
.section{position:absolute;left:12px;width:136px;height:25px;border-radius:13px;background:var(--pill);font-size:7.2px;color:#555;display:flex;align-items:center;padding-left:12px}
.section b{font-weight:400;border-right:1px solid #ccc;padding-right:10px;margin-right:10px}
.ep{position:absolute;left:12px;display:flex;align-items:center;gap:7px;width:145px}
.ep .num{width:20px;height:20px;border-radius:50%;background:#f1f1f4;font-size:7.2px;display:flex;align-items:center;justify-content:center;flex:none}
.ep .num.active{background:var(--play);width:22px;height:22px}
.ep .t{font-size:7.8px;font-weight:500;white-space:nowrap;overflow:hidden;text-overflow:ellipsis;line-height:10px}
.ep .m{font-size:6.3px;color:#555;line-height:10px}

/* footer */
.footer-bg{left:0;top:850px;width:734px;height:350px}
.newsletter{left:0;top:925px;width:734px;text-align:center;color:#fff;font-size:27px;font-weight:600}
.subscribe{left:221px;top:964px;width:284px;height:32px;border-radius:16px;background:#fff;display:flex;align-items:center;padding-left:16px;gap:6px;font-size:8.5px;color:#888}
.subscribe .send{position:absolute;right:7px;top:5px;width:22px;height:22px;border-radius:50%;background:var(--episode);display:flex;align-items:center;justify-content:center}
.f-brand{left:59px;top:1066px;color:#fff;font-size:26px;font-weight:700;letter-spacing:1px;line-height:1}
.f-brand small{display:block;font-size:6px;font-weight:500;letter-spacing:4px;margin-top:6px;padding-left:10px}
.f-col{top:1042px;color:#fff;font-size:8.7px;line-height:16.5px}
.f-col h4{font-size:9px;font-weight:600;color:#8f8f90;letter-spacing:.5px;margin-bottom:7px}
.social{top:1069px;width:26px;height:26px;border-radius:50%;background:#5a5a5b}
.f-rule{left:50px;top:1163px;width:634px;height:1px;background:#5d5d5e}
.copy{left:0;top:1175px;width:734px;text-align:center;font-size:8.7px;color:#fff}
.top-btn{left:691px;top:1151px;width:25px;height:25px;border-radius:50%;background:var(--episode);display:flex;align-items:center;justify-content:center}
</style>
</head>
<body>

<header>
  <div class="abs brand">VORNAQUILL<small>LEARNING CENTRE</small></div>
  <div class="abs nav nav-title">Quillet Tutorial Step by Step</div>
  <div class="abs nav nav-rate"><svg width="10" height="10" viewBox="0 0 24 24"><path fill="#f7941d" d="M12 2l3 7 7 .6-5.3 4.7 1.6 7.4L12 18l-6.3 3.7 1.6-7.4L2 9.6 9 9z"/></svg>Leave a rating</div>
  <div class="abs progress"><i></i>Your progress</div>
  <div class="abs share"><svg width="9" height="8" viewBox="0 0 24 20"><path fill="#fff" d="M14 0l10 9-10 9v-5C7 13 3 15 0 20 1 12 5 6 14 5z"/></svg>SHARE</div>
  <div class="abs kebab"><b></b><b></b><b></b></div>
  <div class="abs rule"></div>
</header>

<main>
  <div class="abs video" role="img" aria-label="Episode video preview showing a purple landing page mock-up">
    <div class="screen"></div>
    <div class="play"><svg width="30" height="36" viewBox="0 0 30 36"><defs><linearGradient id="pg" x1="0" x2="1"><stop offset="0" stop-color="#fbb07a"/><stop offset="1" stop-color="#f47b6e"/></linearGradient></defs><path d="M0 0L30 18 0 36z" fill="url(#pg)"/></svg></div>
  </div>
  <div class="abs arrow" style="left:37px"><svg width="12" height="10" viewBox="0 0 12 10"><path d="M11 5H1M5 1L1 5l4 4" stroke="#222" stroke-width="1.2" fill="none"/></svg></div>
  <div class="abs arrow" style="left:465px"><svg width="12" height="10" viewBox="0 0 12 10"><path d="M1 5h10M7 1l4 4-4 4" stroke="#222" stroke-width="1.2" fill="none"/></svg></div>

  <section class="abs episode">
    <div class="thumb" role="img" aria-label="Series thumbnail"></div>
    <h3>At a Glance</h3>
    <div class="meta"><span>Episode 1</span><span>◷ RUN TIME 2:40</span></div>
    <div class="tags">Tags</div>
    <div class="tag">ANIMATION</div>
    <div class="divider"></div>
    <div class="btn btn-sub">SUBSCRIBE TO SERIES</div>
    <div class="btn btn-watch">WATCHED EPISODE?</div>
    <div class="ico" style="top:5px"><svg width="8" height="8" viewBox="0 0 24 24"><path d="M12 21l-9-9a5 5 0 017-7l2 2 2-2a5 5 0 017 7z" stroke="#fff" stroke-width="2" fill="none"/></svg></div>
    <div class="ico" style="top:26px"><svg width="8" height="8" viewBox="0 0 24 24"><path d="M12 3v12M6 10l6 6 6-6M4 21h16" stroke="#fff" stroke-width="2" fill="none"/></svg></div>
    <div class="ico" style="top:47px"><svg width="8" height="8" viewBox="0 0 24 24"><circle cx="12" cy="12" r="9" stroke="#fff" stroke-width="2" fill="none"/><path d="M12 7v5l3 3" stroke="#fff" stroke-width="2" fill="none"/></svg></div>
  </section>
  <svg class="abs chev" width="6" height="9" viewBox="0 0 6 9"><path d="M1 1l4 3.5L1 8" stroke="#888" stroke-width="1.2" fill="none"/></svg>

  <div class="abs block-head" style="top:541px">About This Episode</div>
  <p class="abs about">Aenean sollicitudin, lorem quis bibendum auctor, nisi elit consequat ipsum, nec sagittis sem nibh id elit. Duis sed odio sit amet nibh vulputate cursus a sit amet mauris. Morbi accumsan ipsum velit.</p>
  <div class="abs published">Published On Sep 9th. 2020</div>

  <div class="abs block-head" style="top:656px">Discuss it</div>
  <div class="abs contribute"><div class="avatar" role="img" aria-label="Member portrait"></div>Contribute to the Discussions</div>

  <div class="abs comment">
    <div class="av" role="img" aria-label="Commenter avatar"></div>
    <div class="name">Brightmoor<span>• 3 month ago</span></div>
    <div class="txt">BEAUTIFUL</div>
    <div class="lvl">Level 7</div>
    <div class="likes"><svg width="8" height="7" viewBox="0 0 24 22"><path d="M12 21L3 12a5 5 0 017-7l2 2 2-2a5 5 0 017 7z" fill="#ccc"/></svg>210</div>
  </div>

  <aside class="abs sidebar">
    <div class="series-thumb" role="img" aria-label="Series thumbnail"></div>
    <div class="series-title">Larkspur 6 From Scratch</div>
    <div class="series-meta"><span>Series</span><span style="color:#f7941d">●●</span><span>44 Lessons</span><span>◷ 4:10:53 hrs</span></div>
    <div class="sb-rule" style="top:81px"></div>

    <div class="section" style="top:98px"><b>Section 1</b>Prerequisites</div>
    <div class="ep" style="top:139px;left:11px"><div class="num active"><svg width="7" height="8" viewBox="0 0 7 8"><path d="M0 0l7 4-7 4z" fill="#fff"/></svg></div><div><div class="t">At a Glance</div><div class="m">Episode 1 &nbsp; ◷ 2:00 hrs</div></div></div>
    <div class="ep" style="top:177px"><div class="num">02</div><div style="min-width:0"><div class="t">Install Runtime, DataStore and comp...</div><div class="m">Episode 2 &nbsp; ◷ 2:00 hrs</div></div></div>
    <div class="ep" style="top:211px"><div class="num">03</div><div><div class="t">The Larkspur Installer</div><div class="m">Episode 3 &nbsp; ◷ 2:00 hrs</div></div></div>
    <div class="ep" style="top:245px"><div class="num">04</div><div><div class="t">Larkspur Valet Setup</div><div class="m">Episode 4 &nbsp; ◷ 2:00 hrs</div></div></div>
    <div class="sb-rule" style="top:287px"></div>

    <div class="section" style="top:309px"><b>Section 2</b>Routing</div>
    <div class="ep" style="top:355px"><div class="num">05</div><div><div class="t">Basic Routing and views</div><div class="m">Episode 5 &nbsp; ◷ 2:00 hrs</div></div></div>
    <div class="ep" style="top:389px"><div class="num">06</div><div><div class="t">Pass request and views</div><div class="m">Episode 6 &nbsp; ◷ 2:00 hrs</div></div></div>
    <div class="ep" style="top:423px"><div class="num">07</div><div><div class="t">Route Wildcards</div><div class="m">Episode 7 &nbsp; ◷ 2:00 hrs</div></div></div>
    <div class="ep" style="top:458px"><div class="num">08</div><div><div class="t">Routing to controllers</div><div class="m">Episode 8 &nbsp; ◷ 2:00 hrs</div></div></div>
    <div class="sb-rule" style="top:497px"></div>

    <div class="section" style="top:519px"><b>Section 3</b>Database Access</div>
    <div class="ep" style="top:564px"><div class="num">09</div><div><div class="t">Setup a database connection</div><div class="m">Episode 9 &nbsp; ◷ 2:00 hrs</div></div></div>
    <div class="ep" style="top:598px"><div class="num">10</div><div><div class="t">Hello Quarry</div><div class="m">Episode 10 &nbsp; ◷ 2:00 hrs</div></div></div>
    <div class="ep" style="top:633px"><div class="num">11</div><div><div class="t">Migrations</div><div class="m">Episode 11 &nbsp; ◷ 2:00 hrs</div></div></div>
  </aside>
</main>

<footer>
  <svg class="abs footer-bg" viewBox="0 0 734 350" preserveAspectRatio="none">
    <path d="M0 128Q367-121 734 150V350H0Z" fill="var(--footer-arc)"/>
    <path d="M0 135Q360-94 734 182V350H0Z" fill="var(--footer)"/>
  </svg>
  <div class="abs newsletter">Newsletter</div>
  <div class="abs subscribe">
    <svg width="11" height="8" viewBox="0 0 22 16"><rect x="1" y="1" width="20" height="14" rx="2" stroke="#aaa" fill="none" stroke-width="1.5"/><path d="M1 2l10 7 10-7" stroke="#aaa" fill="none" stroke-width="1.5"/></svg>
    Enter your email address
    <div class="send"><svg width="10" height="10" viewBox="0 0 24 24"><path d="M22 2L2 10l8 3 3 8z" fill="#fff"/></svg></div>
  </div>

  <div class="abs f-brand">VORNAQUILL<small>LEARNING CENTRE</small></div>
  <div class="abs f-col" style="left:245px"><h4>COMPANY</h4>About<br>Courses<br>FAQs</div>
  <div class="abs f-col" style="left:341px"><h4>GET INVOLVED</h4>Blog<br>Contact</div>
  <div class="abs f-col" style="left:446px"><h4>INFORMATION</h4>Terms of Service<br>Honor Code<br>Privacy Policy</div>
  <div class="abs f-col" style="left:559px"><h4>FOLLOW US</h4></div>
  <div class="abs social" style="left:560px" aria-label="Social profile"></div>
  <div class="abs social" style="left:591px" aria-label="Social profile"></div>
  <div class="abs social" style="left:620px" aria-label="Social profile"></div>
  <div class="abs social" style="left:649px" aria-label="Social profile"></div>

  <div class="abs f-rule"></div>
  <div class="abs copy">© Copyright Vornaquill 2020. All rights reserved.</div>
  <div class="abs top-btn"><svg width="7" height="9" viewBox="0 0 7 9"><path d="M3.5 9V1M1 3.5l2.5-2.5L6 3.5" stroke="#fff" fill="none"/></svg></div>
</footer>

</body>
</html>
```